Ward Compass Business Card Design*

We need a business card design for our company Ward Compass. Our company is specialized in providing online consulting services regarding medical institutions, hospitals and doctors. We work with patients worldwide looking to choose between healthcare providers. We have a website you may use as a reference, where we list doctors and clinics worldwide. So we target Medical providers as well as patients worldwide.
Target Market(s)
Medical Providers and patients around the world
Industry/Entity Type
Medical
Contact Information for Business Card
Salwa Kettani
CEO
+90 612 348 2175
info@wardcompass.example
www.wardcompass.example
14 Annakhil 7 H.R.B. Rabat, Morocco
Requirements
Must have
- Company logo/name on one full side, personal info and smaller logo and company name on the other side.
Nice to have
- Smart and elegant design

```html
<!DOCTYPE html>
<html lang="en">
<head>
<meta charset="utf-8">
<title>Ward Compass Business Card</title>
<link rel="stylesheet" href="https://fonts.googleapis.com/css2?family=Montserrat:wght@500;700&family=Open+Sans:wght@400;600&display=swap">
<style>
  :root {
    --navy: #1d3c6c;
    --navy-dark: #142c52;
    --grey: #7d7f83;
    --text: #3b3d42;
    --card: #f7f7f8;
    --stage: #2c2d30;
  }
  * { box-sizing: border-box; margin: 0; padding: 0; }
  html, body { width: 1200px; height: 997px; overflow: hidden; }
  body {
    background: var(--stage);
    display: flex;
    align-items: center;
    justify-content: center;
    gap: 80px;
    font-family: "Open Sans", Arial, sans-serif;
  }
  .card {
    position: relative;
    width: 380px;
    height: 630px;
    border-radius: 16px;
    overflow: hidden;
    background: linear-gradient(160deg, #ffffff 0%, var(--card) 60%, #e9eaec 100%);
    box-shadow: 0 18px 40px rgba(0,0,0,.5);
  }
  .band {
    position: absolute;
    left: 0; right: 0;
    height: 44px;
    background: var(--navy);
  }
  .band--top { top: 0; }
  .band--bottom { bottom: 0; height: 64px; }
  .stripes {
    position: absolute;
    left: 0; right: 0;
    height: 22px;
    background: repeating-linear-gradient(to bottom, var(--navy) 0 3px, transparent 3px 8px);
  }
  .stripes--top { top: 50px; }
  .stripes--bottom { bottom: 70px; }

  .brand {
    display: flex;
    align-items: center;
    gap: 12px;
  }
  .brand__dot {
    border-radius: 50%;
    background: var(--navy);
    flex: none;
  }
  .brand__name {
    font-family: "Montserrat", Arial, sans-serif;
    font-weight: 700;
    color: var(--navy);
    letter-spacing: 1px;
    text-transform: uppercase;
    white-space: nowrap;
  }

  /* front */
  .card--front .brand {
    position: absolute;
    top: 270px; left: 0; right: 0;
    flex-direction: column;
    gap: 18px;
  }
  .card--front .brand__dot { width: 64px; height: 64px; }
  .card--front .brand__name { font-size: 34px; }

  /* back */
  .card--back .brand {
    position: absolute;
    top: 104px; left: 40px;
  }
  .card--back .brand__dot { width: 40px; height: 40px; }
  .card--back .brand__name { font-size: 21px; }

  .person {
    position: absolute;
    top: 200px; left: 0; right: 0;
    text-align: center;
    font-family: "Montserrat", Arial, sans-serif;
    font-weight: 700;
  }
  .person__name { color: var(--navy); font-size: 20px; letter-spacing: .5px; }
  .person__role { color: var(--grey); font-size: 15px; margin-top: 2px; }

  .divider {
    position: absolute;
    left: 95px; right: 95px;
    height: 3px;
    background: linear-gradient(to right, transparent, var(--navy) 50%, transparent);
  }
  .divider--one { top: 285px; }
  .divider--two { top: 420px; }

  .contact {
    position: absolute;
    left: 0; right: 0;
    text-align: center;
    color: var(--text);
    font-size: 15px;
    line-height: 1.55;
  }
  .contact--direct { top: 305px; }
  .contact--web { top: 440px; }
  .contact__icons {
    display: flex;
    justify-content: center;
    gap: 14px;
    margin-bottom: 6px;
  }
  .contact__icons svg { width: 16px; height: 16px; fill: var(--navy); }
  .contact__site {
    color: var(--navy);
    font-weight: 600;
    font-size: 16px;
    margin-top: 6px;
  }
  .tagline {
    position: absolute;
    bottom: 0; left: 0; right: 0;
    height: 64px;
    line-height: 64px;
    text-align: center;
    color: #ffffff;
    font-size: 14px;
    letter-spacing: .3px;
  }
</style>
</head>
<body>
  <section class="card card--front" aria-label="Business card front">
    <div class="band band--top"></div>
    <div class="stripes stripes--top"></div>
    <div class="brand">
      <span class="brand__dot"></span>
      <span class="brand__name">Ward Compass</span>
    </div>
    <div class="stripes stripes--bottom"></div>
    <div class="band band--bottom"></div>
  </section>

  <section class="card card--back" aria-label="Business card back">
    <div class="band band--top"></div>
    <div class="stripes stripes--top"></div>
    <div class="brand">
      <span class="brand__dot"></span>
      <span class="brand__name">Ward Compass</span>
    </div>
    <div class="person">
      <p class="person__name">SALWA KETTANI</p>
      <p class="person__role">CEO</p>
    </div>
    <div class="divider divider--one"></div>
    <div class="contact contact--direct">
      <div class="contact__icons">
        <svg viewBox="0 0 24 24" aria-label="Phone"><path d="M6.6 10.8a15 15 0 0 0 6.6 6.6l2.2-2.2a1 1 0 0 1 1-.25 11.4 11.4 0 0 0 3.6.57 1 1 0 0 1 1 1V20a1 1 0 0 1-1 1A17 17 0 0 1 3 4a1 1 0 0 1 1-1h3.5a1 1 0 0 1 1 1c0 1.25.2 2.45.57 3.6a1 1 0 0 1-.25 1z"/></svg>
        <svg viewBox="0 0 24 24" aria-label="Email"><path d="M2 5h20v14H2zm2 2v.5l8 5 8-5V7l-8 5z"/></svg>
      </div>
      <p>+90 612 348 2175</p>
      <p>info@wardcompass.example</p>
    </div>
    <div class="divider divider--two"></div>
    <div class="contact contact--web">
      <div class="contact__icons">
        <svg viewBox="0 0 24 24" aria-label="Website"><path d="M12 2a10 10 0 1 0 0 20 10 10 0 0 0 0-20zm6.9 6h-3a15 15 0 0 0-1.4-3.9A8 8 0 0 1 18.9 8zM12 4c.8 1.2 1.5 2.5 1.9 4h-3.8c.4-1.5 1.1-2.8 1.9-4zM4.3 14a8 8 0 0 1 0-4h3.4a16 16 0 0 0 0 4zm.8 2h3a15 15 0 0 0 1.4 3.9A8 8 0 0 1 5.1 16zm3-8h-3a8 8 0 0 1 4.4-3.9A15 15 0 0 0 8.1 8zM12 20c-.8-1.2-1.5-2.5-1.9-4h3.8c-.4 1.5-1.1 2.8-1.9 4zm2.3-6H9.7a14 14 0 0 1 0-4h4.6a14 14 0 0 1 0 4zm.2 5.9A15 15 0 0 0 15.9 16h3a8 8 0 0 1-4.4 3.9zm1.8-5.9a16 16 0 0 0 0-4h3.4a8 8 0 0 1 0 4z"/></svg>
      </div>
      <p class="contact__site">www.wardcompass.example</p>
    </div>
    <div class="stripes stripes--bottom"></div>
    <div class="band band--bottom"></div>
    <p class="tagline">Find &amp; compare top rated clinics world wide</p>
  </section>
</body>
</html>
```